Revamp Kestrelo Inc website

A complete revamp of the www.kestrelo-app.com website.
Strong actionable landing pages.
An in-house site was being done but was abandoned. See http://www.sitebuildly.com/dmorvane/kestrelo and once in, click on the "Home" to go to the main Home page.
Updates

A new YouTube Standard Video has just been posted: http://www.clipvista.com/watch?v=Q-T8ma4zLpW&feature=email

I thought that I would share what was being done in-house, but was abandoned.

Once launched you will come to the main landing page, then click on the "Home" button to see the main home page. I thought this was rather interesting. One problem here is Flash, most smartphones don't support Flash and our market is in that world, so Flash really is not a good option.

Reason: Please can you submit one more design, we have a dead tie with voting.

Reason: Request as per a designer.

Target Market(s)

Kestrelo for all intense purposes is mobile RoadHalo on steroids. Currently running on Robodroid, BB and OrchardPhone. End of Jan 2012 we will run on ANY J2ME (Java) supported phone as well. Here we will be talking directly to the OBD (onboard diagnostics) in the car. In the event of the car's airbags being deployed emergency services, ES, (whether public, 911 or other country equivalent, or private, alarm company) the application will not only call the ES but also log the gps information. Other services include: SOS, Nurse Lines, Roadside, Notify Friends and Family.
Kestrelo determines the ERC by the phones location, thus assuming not private in the USA will reach out to 911, Europe 112 etc.

Kestrelo is about making a pro and re active emergency solution to the masses. It must be affordable to anyone owning a cell phone (thus: 9 cents per day). The emphasis is on the person not the asset as RoadHalo and other competitors are. It must be adaptable to ones environment

Kestrelo target market sale is a top-down (Corporate to consumer) we do offer:
* white-labeling (see www.guardlinemobileus.com) as well as non branded solutions (Kestrelo branded),
* private emergency response center call and data routing - here the emergency call is routed the the companies emergency call center (example: alarm company, security firm, campus police), and the location and user details data details on file are pushed as well.

As such our target corporate market primarily is:
Security, Home Alarm, Insurance, University Campus Police, Auto, Smartphone users, Roadside assistance

Our ultimate target audience is cell phone users, where security, safety and peace of mind of oneself, family and/or team members is of importance.

Requirements
Must have
• Must have strong actionable call to action features
Must have multiple actionable landing pages
Must link to our ecommerce
Must link into blog
Must be able to cellphone friendly (i.e.: no flash)
Must be SEO

```html
<!DOCTYPE html>
<html lang="en">
<head>
<meta charset="utf-8">
<title>Kestrelo, Inc. – Mobile GPS Tracking</title>
<link rel="stylesheet" href="https://fonts.googleapis.com/css2?family=Yanone+Kaffeesatz:wght@300;400&family=Arimo:ital,wght@0,400;0,700;1,400&display=swap">
<style>
:root{
  --page:#ececec;
  --panel:#ffffff;
  --nav:#2b2b2b;
  --nav-active:#4a4a4a;
  --ink:#333333;
  --muted:#8a8a8a;
  --accent:#2a8fc1;
  --accent-dark:#1e6fa0;
  --footer:#1f1f1f;
  --footer-line:#4a4a4a;
  --bullet:#8a2f8f;
}
*{box-sizing:border-box;margin:0;padding:0}
html,body{width:827px;height:1200px;overflow:hidden}
body{position:relative;background:var(--page);font-family:"Arimo",Arial,sans-serif;color:var(--ink)}
.abs{position:absolute}
.site-header{left:0;top:0;width:827px;height:62px;background:linear-gradient(#e2e2e2,#d9d9d9)}
.brand{left:98px;top:22px;font-family:"Yanone Kaffeesatz",sans-serif;font-weight:300;font-size:26px;color:#222}
.brand-rule{left:206px;top:19px;width:1px;height:32px;background:#aaa}
.tagline{left:219px;top:19px;font-size:10.5px;line-height:19px;font-style:italic;color:var(--accent)}
.contact{left:630px;top:24px;font-size:9.5px;line-height:16px;font-style:italic;color:#222}
.main-nav{left:97px;top:62px;width:633px;height:28px;background:var(--nav);display:flex;align-items:center;justify-content:space-around;padding:0 4px}
.main-nav a{color:#fff;text-decoration:none;font-size:9.5px;padding:3px 9px}
.main-nav a.active{background:var(--nav-active)}
.panel{background:var(--panel);box-shadow:0 14px 18px -10px rgba(0,0,0,.35)}
.hero-panel{left:97px;top:90px;width:633px;height:272px}
.hero-art{left:8px;top:8px;width:616px;height:199px;background:linear-gradient(100deg,#8fc4e8 0%,#5e9e3e 30%,#6fb0de 52%,#7fae4a 72%,#c9a04a 100%)}
.hero-title{left:10px;top:164px;font-family:"Yanone Kaffeesatz",sans-serif;font-weight:300;font-size:24px;color:#fff}
.hero-intro{left:0;top:224px;width:633px;text-align:center;font-size:9.2px;line-height:18px;font-style:italic;color:var(--muted);white-space:nowrap}
.info-panel{left:97px;top:392px;width:634px;height:258px}
.section-title{font-family:"Yanone Kaffeesatz",sans-serif;font-weight:400;font-size:17px;color:var(--accent)}
.features{left:11px;top:10px;width:372px}
.features p{margin-top:11px;font-size:8.4px;line-height:17.5px}
.feature-cols{position:relative;margin-top:14px;height:132px}
.feature-list{position:absolute;top:0;list-style:none;font-size:8.4px;line-height:18.7px;white-space:nowrap}
.feature-list.left{left:0;width:172px}
.feature-list.right{left:172px;width:200px}
.feature-list li{position:relative;padding-left:24px}
.feature-list li::before{content:"";position:absolute;left:2px;top:2px;width:14px;height:14px;border-radius:50%;background:radial-gradient(circle,var(--bullet) 0 3px,#d9c0dc 4px 5px,#efe5f0 6px)}
.col-rule{left:386px;top:12px;width:1px;height:234px;background:#555}
.testimonials{left:396px;top:10px;width:232px;font-size:8.2px;line-height:17.2px}
.testimonials blockquote{margin-top:11px}
.testimonials cite{color:var(--accent);font-style:italic}
.testimonials .inline-cite{float:right;padding-right:8px}
.testimonials .block-cite{display:block;text-align:right;padding-right:2px}
.testimonials .t-second{margin-top:18px}
.read-more{right:7px;bottom:8px;font-size:7.5px;font-style:italic;color:var(--accent-dark)}
.app-shot{left:98px;top:693px;width:208px;height:327px;background:linear-gradient(#f2f2f2 0 10px,#dfe6ee 10px 75px,#1e4c8f 75px 280px,#e8e8e8 280px)}
.cta{left:198px;top:1028px;width:107px;height:23px;background:var(--accent);color:#fff;font-size:9px;font-style:italic;text-align:center;line-height:23px;text-decoration:none}
.video{left:318px;top:693px;width:413px;height:251px;background:#000}
.video-frame{left:51px;top:0;width:311px;height:230px;background:linear-gradient(160deg,#0f3e48,#1c7a7e 55%,#0d2c34)}
.video-quote{left:14px;top:28px;width:283px;text-align:center;color:#fff;font-size:13.5px;line-height:18.5px}
.video-bar{left:0;top:230px;width:413px;height:21px;background:#1b1b1b}
.video-notes{left:319px;top:960px;width:410px;font-size:8px;line-height:17.5px;font-style:italic;color:var(--muted)}
.site-footer{left:0;top:1060px;width:827px;height:140px;background:var(--footer);color:#fff}
.foot-col h3{font-family:"Yanone Kaffeesatz",sans-serif;font-weight:300;font-size:15.5px;color:#fff;margin-bottom:5px;white-space:nowrap}
.foot-col ul{list-style:none;padding-left:11px;font-size:8.6px;line-height:16px}
.foot-rule{left:98px;top:92px;width:633px;height:1px;background:var(--footer-line)}
.foot-brand{left:101px;top:100px;font-family:"Yanone Kaffeesatz",sans-serif;font-weight:300;font-size:24px}
.social{left:648px;top:100px;display:flex;gap:5px}
.social span{width:17px;height:17px;display:block}
.copyright{left:626px;top:124px;font-size:7.5px;font-style:italic}
</style>
</head>
<body>
<header class="site-header abs">
  <div class="brand abs">Kestrelo, Inc.</div>
  <div class="brand-rule abs"></div>
  <div class="tagline abs">Kestrelo | Accident Response, Personal GPS Tracker,<br>Mobile GPS Tracking, Roadside</div>
  <div class="contact abs">Phone: xxxx xx xx xx<br>Email: info@sitename.com</div>
</header>
<nav class="main-nav abs">
  <a class="active" href="#">Home</a><a href="#">About Us</a><a href="#">Services</a><a href="#">Partners</a><a href="#">Testimonials</a><a href="#">Contact Us</a><a href="#">Purchase</a><a href="#">Login</a>
</nav>
<section class="hero-panel panel abs">
  <div class="hero-art abs" role="img" aria-label="World map with a smartphone sending a location signal">
    <div class="hero-title abs">Mobile GPS Tracking</div>
  </div>
  <p class="hero-intro abs">Now you can carry confidence with you all the time: introducing Kestrelo, the ultimate mobile solution for automatic emergency alerts and response . . .<br>all for 9 cents per day.</p>
</section>
<section class="info-panel panel abs">
  <div class="features abs">
    <h2 class="section-title">Features</h2>
    <p>No matter the emergency, Kestrelo instantaneously triggers an emergency response call conveying your exact location and other critical information to emergency personnel.&nbsp; Kestrelo’s comprehensive service also provides the following features:</p>
    <div class="feature-cols">
      <ul class="feature-list left">
        <li>Accident and Impact Management<br>(patent pending)</li>
        <li>International and National SOS</li>
        <li>Personal Location Notification</li>
        <li>24/7 Certified Nurse Line</li>
        <li>Auto Assistance</li>
        <li>Weather Alert</li>
      </ul>
      <ul class="feature-list right">
        <li>High Crime Area Alerts</li>
        <li>Cyber Alert Notification Management</li>
        <li>Homeland and Travel Status Notification</li>
        <li>Traffic Alerts</li>
        <li>Extensive Online Tracking Management Portal</li>
        <li>Including: Geo-Fencing, Trip Reporting, Speed<br>Reporting, Incident Tracking and Reporting</li>
      </ul>
    </div>
  </div>
  <div class="col-rule abs"></div>
  <div class="testimonials abs">
    <h2 class="section-title">Testimonials</h2>
    <blockquote>I drive 40 minutes to work at 2 in the morning. If I were to get in an accident, work would assume I was sick, and my wife would be home sleeping peacefully. I feel much safer knowing that I have someone watching over me and making sure I travel safely with the Kestrelo smart-phone app. Great job, Kestrelo!” - <cite class="inline-cite">Dana Whitfield</cite></blockquote>
    <blockquote class="t-second">“...Knocked out, my car completely trashed, I woke up to find the police and ambulance had already been informed by Kestrelo. Thanks Kestrelo for doing what you said you would” - <cite class="block-cite">Marcus</cite></blockquote>
  </div>
  <a class="read-more abs" href="#">Read more...</a>
</section>
<div class="app-shot abs" role="img" aria-label="Kestrelo app screen showing SOS, notify, repair, nurse and impact buttons, traffic, alerts, crime, weather and map status, with supported phone platforms Robodroid, OrchardPhone and Blackreed"></div>
<a class="cta abs" href="#">Get It Now - Kestrelo</a>
<div class="video abs">
  <div class="video-frame abs" role="img" aria-label="Video still with a glowing teal digital background">
    <p class="video-quote abs">“We have now entered the third wave of mobile. First was communication, second was content and now the third is context. Context is restructuring mobile services so that it utilizes contextual data points to optimize the service experience for the users...</p>
  </div>
  <div class="video-bar abs">
    <svg width="413" height="21" viewBox="0 0 413 21">
      <rect x="0" y="0" width="413" height="3" fill="#444"/><rect x="0" y="0" width="22" height="3" fill="#c00"/>
      <rect x="17" y="8" width="2.5" height="8" fill="#ddd"/><rect x="22" y="8" width="2.5" height="8" fill="#ddd"/>
      <path d="M42 10h3l4-3v10l-4-3h-3z" fill="#ddd"/>
      <text x="65" y="15" fill="#ccc" font-size="8" font-family="Arimo,sans-serif">0:09 / 3:28</text>
      <text x="333" y="15" fill="#ccc" font-size="7" font-family="Arimo,sans-serif">360p</text>
      <rect x="360" y="8" width="12" height="8" fill="#bbb"/><rect x="376" y="8" width="14" height="8" fill="#888"/><rect x="394" y="7" width="14" height="10" fill="none" stroke="#bbb"/>
    </svg>
  </div>
</div>
<p class="video-notes abs">Video Comments goes here, Just for 9 cents per day, you and your loved ones can rest easy. Kestrelo Smartphone Application (supporting Robodroid, Blackreed and OrchardPhone) gives you..<br>Video Comments goes here, Just for 9 cents per day, you and your loved ones can rest easy. Kestrelo Smartphone Application (supporting Robodroid, Blackreed and OrchardPhone) gives you..</p>
<footer class="site-footer abs">
  <div class="foot-col abs" style="left:98px;top:12px"><h3>Application Download</h3><ul><li>Blackreed</li><li>OrchardPhone</li><li>Robodroid</li></ul></div>
  <div class="foot-col abs" style="left:267px;top:12px"><h3>Kestrelo Services and Policies</h3><ul><li>Privacy Policy</li><li>Terms &amp; Conditions</li></ul></div>
  <div class="foot-col abs" style="left:433px;top:12px"><h3>Company/Marketing</h3><ul><li>Affiliate Program</li></ul></div>
  <div class="foot-col abs" style="left:588px;top:12px"><h3>Kestrelo News and Events</h3><ul><li>News and Events</li><li>Live Chat</li></ul></div>
  <div class="foot-rule abs"></div>
  <div class="foot-brand abs">Kestrelo, Inc.</div>
  <div class="social abs"><span style="background:#3b5998"></span><span style="background:#33a9dc"></span><span style="background:#d6157f"></span><span style="background:#1c80b4"></span></div>
  <div class="copyright abs">Copyright 2011 @kestrelo-app.com</div>
</footer>
</body>
</html>
```